Harborline Renewal Business Card Design

Professional and clean design. The design colors should flow with the logo. Two-sided card with the website on the back which is:

www.HarborlineRenewal.example.

"Specializing in Water Damage Restoration"

On the front I need the name, email, phone, and logo.

Name: Darnell Quisby
Email: Darnell@HarborlineRenewal.example
Phone: 555-318-2046 for now

I only have the Preview and Thumbnail right now but should have the source files uploaded within a day or two.

Target Market(s)

Flood victims, home owners with water damage from busted pipes etc...

Industry/Entity Type

Business

Contact Information for Business Card

Name: Darnell Quisby

Font styles to use
Serif
Sans Serif

Requirements
Must have
• Business Card Details Info

```html
<!DOCTYPE html>
<html lang="en">
<head>
<meta charset="utf-8">
<title>Harborline Renewal Business Card</title>
<link rel="stylesheet" href="https://fonts.googleapis.com/css2?family=Cinzel:wght@600&family=Open+Sans:wght@400;700&display=swap">
<style>
  :root {
    --page: #e8e5e0;
    --brand-blue: #2f96d6;
    --wave-blue: #55bdec;
    --line-blue: #2a8fd0;
    --white: #ffffff;
    --card-shadow: rgba(0, 0, 0, 0.18);
  }
  * { margin: 0; padding: 0; box-sizing: border-box; }
  html, body { width: 1200px; height: 950px; overflow: hidden; }
  body { background: var(--page); position: relative; font-family: "Open Sans", sans-serif; }

  .card {
    position: absolute;
    width: 700px;
    height: 400px;
    border-radius: 4px;
    overflow: hidden;
    box-shadow: 0 10px 28px var(--card-shadow);
  }
  .card--back { left: 150px; top: 45px; background: var(--brand-blue); }
  .card--front { left: 350px; top: 505px; background: var(--white); }

  .brand-mark {
    position: absolute;
    display: flex;
    flex-direction: column;
    align-items: center;
  }
  .brand-mark__dot { width: 58px; height: 58px; border-radius: 50%; margin-bottom: 12px; }
  .brand-mark__name {
    font-family: "Cinzel", serif;
    font-weight: 600;
    font-size: 31px;
    letter-spacing: 1px;
    white-space: nowrap;
  }
  .card--back .brand-mark { left: 0; right: 0; top: 105px; }
  .card--back .brand-mark__dot { background: var(--white); }
  .card--back .brand-mark__name { color: var(--white); }

  .tagline {
    position: absolute;
    left: 0; right: 0; top: 265px;
    text-align: center;
    color: var(--white);
    font-size: 17px;
  }

  .wave { position: absolute; inset: 0; }
  .card--front .brand-mark { left: 110px; width: 380px; top: 36px; }
  .card--front .brand-mark__dot { background: var(--brand-blue); }
  .card--front .brand-mark__name { color: var(--brand-blue); }

  .contact { position: absolute; color: var(--white); font-size: 16px; }
  .contact__name { left: 380px; top: 214px; font-weight: 700; font-size: 22px; }
  .contact__row { display: flex; align-items: center; gap: 8px; white-space: nowrap; }
  .contact__row svg { width: 18px; height: 18px; flex: none; }
  .contact__phone { left: 70px; top: 318px; }
  .contact__email { left: 350px; top: 268px; }
  .contact__web { left: 350px; top: 300px; }
</style>
</head>
<body>

<section class="card card--back" aria-label="Business card, back">
  <div class="brand-mark">
    <div class="brand-mark__dot"></div>
    <div class="brand-mark__name">HARBORLINE RENEWAL</div>
  </div>
  <p class="tagline">Specializing in Water Damage Restoration</p>
</section>

<section class="card card--front" aria-label="Business card, front">
  <svg class="wave" viewBox="0 0 700 400" preserveAspectRatio="none" aria-hidden="true">
    <path d="M0,262 C200,292 350,192 450,162 C560,127 640,72 700,42" fill="none" stroke="var(--line-blue)" stroke-width="3"/>
    <path d="M0,278 C200,308 350,208 450,178 C560,143 640,88 700,58 L700,400 L0,400 Z" fill="var(--wave-blue)"/>
  </svg>

  <div class="brand-mark">
    <div class="brand-mark__dot"></div>
    <div class="brand-mark__name">HARBORLINE RENEWAL</div>
  </div>

  <div class="contact contact__name">Darnell Quisby</div>

  <div class="contact contact__row contact__email">
    <svg viewBox="0 0 24 24" aria-hidden="true"><rect x="2" y="5" width="20" height="14" rx="1.5" fill="var(--white)"/><path d="M3 6l9 7 9-7" fill="none" stroke="var(--wave-blue)" stroke-width="1.8"/></svg>
    <span>Darnell@HarborlineRenewal.example</span>
  </div>

  <div class="contact contact__row contact__web">
    <svg viewBox="0 0 24 24" aria-hidden="true"><circle cx="12" cy="12" r="10" fill="var(--white)"/><path d="M2 12h20M12 2c3 3 3 17 0 20M12 2c-3 3-3 17 0 20" fill="none" stroke="var(--wave-blue)" stroke-width="1.5"/></svg>
    <span>HarborlineRenewal.example</span>
  </div>

  <div class="contact contact__row contact__phone">
    <svg viewBox="0 0 24 24" aria-hidden="true"><path d="M6.6 10.8a15 15 0 0 0 6.6 6.6l2.2-2.2a1 1 0 0 1 1-.25 11.4 11.4 0 0 0 3.6.57 1 1 0 0 1 1 1V20a1 1 0 0 1-1 1A17 17 0 0 1 3 4a1 1 0 0 1 1-1h3.5a1 1 0 0 1 1 1c0 1.25.2 2.45.57 3.57a1 1 0 0 1-.25 1z" fill="var(--white)"/></svg>
    <span>555-318-2046 for now</span>
  </div>
</section>

</body>
</html>
```